Redesign of the UI of a customer service platform

To improve the user experience of our customers, we need a new design for our agent interface of our customer service platform (velorant.com).
The focus will be on the dashboard and the inbox screens (see attached) along with the common UI elements (Buttons, menu, fonts, forms...)
We want a simple and distinctive design

Target Market(s)

Worldwide

Industry/Entity Type

It Service

Number of Pages Required

3 page

Font styles to use
Sans Serif

Requirements
Must have
• New Onboarding page: this is a new page that is shown to user the first time they login to the platform. This will replace the current onboarding screen (setup SMS, Setup widget...etc)
• Dashboard page: to access important information and activate services (see screenshot from current site)
• Inbox page: to manage all the interactions with customers. (see screenshot from current site)
• UI elements (buttons, menus, forms, tables, fonts, color palette)

```html
<!DOCTYPE html>
<html lang="en">
<head>
<meta charset="utf-8">
<title>Velorant – Get Started</title>
<link rel="stylesheet" href="https://fonts.googleapis.com/css2?family=Asap:wght@400;500&family=Slabo+27px&display=swap">
<style>
  :root {
    --brand: #f2502a;
    --nav-bg: #3b3b3b;
    --nav-divider: #464646;
    --nav-text: #ffffff;
    --page-bg: #f2f2f2;
    --heading: #333333;
    --icon-grey: #bdbdbd;
    --track: #d9d9d9;
    --muted: #b0b0b0;
    --badge-red: #e02020;
    --badge-amber: #f5b800;
    --online: #2eb82e;
  }
  * { box-sizing: border-box; margin: 0; padding: 0; }
  html, body { width: 1200px; height: 831px; overflow: hidden; }
  body { background: var(--page-bg); font-family: "Asap", Arial, sans-serif; color: var(--heading); position: relative; }

  .topbar { position: absolute; left: 0; top: 0; width: 1200px; height: 83px; background: var(--nav-bg); display: flex; }
  .brand-tile { width: 83px; height: 83px; background: var(--brand); display: flex; align-items: center; justify-content: center; }
  .nav-item { width: 84px; height: 83px; border-right: 1px solid var(--nav-divider); display: flex; flex-direction: column; align-items: center; justify-content: center; color: var(--nav-text); font-size: 13px; position: relative; }
  .nav-item svg { width: 26px; height: 26px; margin-bottom: 7px; }
  .count { position: absolute; top: 17px; left: 50px; width: 22px; height: 22px; border-radius: 50%; color: #fff; font-size: 12px; display: flex; align-items: center; justify-content: center; }
  .count.red { background: var(--badge-red); }
  .count.amber { background: var(--badge-amber); }
  .agent-avatar { position: absolute; right: 14px; top: 14px; width: 56px; height: 56px; border-radius: 50%; background: radial-gradient(circle at 50% 45%, #d9b59c, #6f5a4d 70%, #e6e6e6 71%); border: 2px solid #eee; }
  .online-dot { position: absolute; right: 62px; top: 14px; width: 14px; height: 14px; border-radius: 50%; background: var(--online); }

  .page-title { position: absolute; top: 120px; width: 100%; text-align: center; font-family: "Slabo 27px", Georgia, serif; font-size: 31px; font-weight: 400; letter-spacing: 0.5px; }
  .video-frame { position: absolute; left: 344px; top: 196px; width: 513px; height: 299px; background: linear-gradient(120deg, #8a5a44 0%, #d9cbbd 35%, #efe6d8 55%, #a27a60 80%, #4a3a32 100%); }
  .play-button { position: absolute; left: 222px; top: 115px; width: 70px; height: 70px; border-radius: 50%; background: rgba(255,255,255,0.85); display: flex; align-items: center; justify-content: center; }
  .player-bar { position: absolute; left: 344px; top: 511px; width: 513px; height: 12px; display: flex; align-items: center; font-size: 11px; color: var(--muted); }
  .player-bar .time { margin: 0 10px 0 6px; }
  .track { flex: 1; height: 3px; background: var(--track); position: relative; }
  .track span { position: absolute; left: 0; top: 0; height: 3px; width: 50%; background: var(--brand); }

  .section-title { position: absolute; top: 571px; width: 100%; text-align: center; font-family: "Slabo 27px", Georgia, serif; font-size: 21px; font-weight: 400; }
  .addons { position: absolute; top: 650px; left: 196px; display: flex; }
  .addon { width: 161.5px; display: flex; flex-direction: column; align-items: center; position: relative; }
  .addon-icon { width: 72px; height: 72px; display: flex; align-items: center; justify-content: center; }
  .addon-name { margin-top: 28px; font-size: 19px; }
  .watch-link { margin-top: 10px; font-size: 13px; color: var(--brand); display: flex; align-items: center; gap: 4px; }
  .selected-tick { position: absolute; top: -4px; left: 40px; }
</style>
</head>
<body>
<header class="topbar">
  <div class="brand-tile" aria-label="velorant.com">
    <svg width="42" height="42" viewBox="0 0 42 42"><circle cx="21" cy="21" r="15" fill="#fff"/></svg>
  </div>
  <div class="nav-item">
    <svg viewBox="0 0 26 26"><path d="M3 14h6l2 3h4l2-3h6v8H3z" fill="#fff"/><path d="M13 3v9M9 8l4 4 4-4" stroke="#fff" stroke-width="2.4" fill="none"/></svg>Inbox
    <span class="count red">4</span>
  </div>
  <div class="nav-item">
    <svg viewBox="0 0 26 26"><rect x="4" y="3" width="16" height="20" fill="none" stroke="#fff" stroke-width="2"/><path d="M8 8h8M8 12h8M8 16h4" stroke="#fff" stroke-width="2"/></svg>Tasks
    <span class="count amber">1</span>
  </div>
  <div class="nav-item">
    <svg viewBox="0 0 26 26"><circle cx="13" cy="8" r="5" fill="#fff"/><path d="M3 24c0-6 4-9 10-9s10 3 10 9z" fill="#fff"/></svg>Customers
  </div>
  <div class="nav-item">
    <svg viewBox="0 0 26 26"><path d="M2 4l22 9-22 9 3-9z M5 13h10" fill="none" stroke="#fff" stroke-width="2" stroke-linejoin="round"/></svg>Campaigns
  </div>
  <div class="nav-item">
    <svg viewBox="0 0 26 26"><text x="13" y="21" text-anchor="middle" font-family="Asap, sans-serif" font-size="22" fill="#fff">$</text></svg>Payments
  </div>
  <div class="nav-item">
    <svg viewBox="0 0 26 26"><path d="M4 3v20M10 8v15M16 3v20M22 12v11" stroke="#fff" stroke-width="2.4"/></svg>Reports
  </div>
  <div class="nav-item">
    <svg viewBox="0 0 26 26"><circle cx="13" cy="13" r="8" fill="none" stroke="#fff" stroke-width="5" stroke-dasharray="3.2 3"/><circle cx="13" cy="13" r="6" fill="#fff"/><circle cx="13" cy="13" r="2.5" fill="#3b3b3b"/></svg>Settings
  </div>
  <span class="online-dot"></span>
  <div class="agent-avatar" role="img" aria-label="Agent profile photo"></div>
</header>

<h1 class="page-title">Get Started</h1>

<div class="video-frame" role="img" aria-label="Video still: colleagues pointing at papers on an office desk">
  <div class="play-button">
    <svg width="20" height="22" viewBox="0 0 20 22"><path d="M2 1l17 10L2 21z" fill="#f2502a"/></svg>
  </div>
</div>
<div class="player-bar">
  <svg width="8" height="10" viewBox="0 0 8 10"><path d="M0 0l8 5-8 5z" fill="#b0b0b0"/></svg>
  <span class="time">0:00</span>
  <div class="track"><span></span></div>
</div>

<h2 class="section-title">Select Your Add-ons</h2>

<div class="addons">
  <div class="addon">
    <div class="addon-icon">
      <svg width="68" height="62" viewBox="0 0 68 62"><rect x="2" y="2" width="64" height="44" rx="3" fill="none" stroke="#bdbdbd" stroke-width="4"/><rect x="8" y="8" width="52" height="30" fill="#bdbdbd"/><path d="M26 48h16l3 10H23z" fill="#bdbdbd"/><rect x="18" y="57" width="32" height="4" fill="#bdbdbd"/></svg>
    </div>
    <div class="addon-name">Campaigns</div>
    <div class="watch-link"><svg width="12" height="12" viewBox="0 0 12 12"><circle cx="6" cy="6" r="5" fill="none" stroke="#f2502a" stroke-width="1.3"/><path d="M5 3.5l2.5 2.5L5 8.5" fill="none" stroke="#f2502a" stroke-width="1.3"/></svg>Watch Video</div>
  </div>
  <div class="addon">
    <div class="addon-icon">
      <svg width="56" height="56" viewBox="0 0 56 56"><circle cx="28" cy="28" r="26" fill="#bdbdbd"/></svg>
    </div>
    <div class="addon-name">Chatline</div>
    <div class="watch-link"><svg width="12" height="12" viewBox="0 0 12 12"><circle cx="6" cy="6" r="5" fill="none" stroke="#f2502a" stroke-width="1.3"/><path d="M5 3.5l2.5 2.5L5 8.5" fill="none" stroke="#f2502a" stroke-width="1.3"/></svg>Watch Video</div>
  </div>
  <div class="addon">
    <svg class="selected-tick" width="26" height="26" viewBox="0 0 26 26"><circle cx="13" cy="13" r="12" fill="#2eb82e"/><path d="M7 13l4 4 8-8" fill="none" stroke="#fff" stroke-width="2.6"/></svg>
    <div class="addon-icon">
      <svg width="64" height="62" viewBox="0 0 64 62"><path d="M32 2C15 2 2 12 2 27c0 8 4 14 10 18l-4 15 14-10c3 1 6 1 10 1 17 0 30-10 30-24S49 2 32 2z" fill="#bdbdbd"/><path d="M18 20h28M18 28h28M18 36h22" stroke="#f2f2f2" stroke-width="2.5"/></svg>
    </div>
    <div class="addon-name">SMS</div>
    <div class="watch-link"><svg width="12" height="12" viewBox="0 0 12 12"><circle cx="6" cy="6" r="5" fill="none" stroke="#f2502a" stroke-width="1.3"/><path d="M5 3.5l2.5 2.5L5 8.5" fill="none" stroke="#f2502a" stroke-width="1.3"/></svg>Watch Video</div>
  </div>
  <div class="addon">
    <div class="addon-icon">
      <svg width="56" height="56" viewBox="0 0 56 56"><circle cx="28" cy="28" r="26" fill="#bdbdbd"/></svg>
    </div>
    <div class="addon-name">Wirepost</div>
    <div class="watch-link"><svg width="12" height="12" viewBox="0 0 12 12"><circle cx="6" cy="6" r="5" fill="none" stroke="#f2502a" stroke-width="1.3"/><path d="M5 3.5l2.5 2.5L5 8.5" fill="none" stroke="#f2502a" stroke-width="1.3"/></svg>Watch Video</div>
  </div>
  <div class="addon">
    <div class="addon-icon">
      <svg width="50" height="66" viewBox="0 0 50 66"><text x="25" y="58" text-anchor="middle" font-family="Asap, sans-serif" font-size="66" fill="#bdbdbd">$</text></svg>
    </div>
    <div class="addon-name">Payment</div>
    <div class="watch-link"><svg width="12" height="12" viewBox="0 0 12 12"><circle cx="6" cy="6" r="5" fill="none" stroke="#f2502a" stroke-width="1.3"/><path d="M5 3.5l2.5 2.5L5 8.5" fill="none" stroke="#f2502a" stroke-width="1.3"/></svg>Watch Video</div>
  </div>
</div>
</body>
</html>
```